diamondscoutline.net - Social Media Branding

diamondscoutline.net --> Social Media Re-Branding & Graphics
Facebook: @dmndscoutline - Instagram: @diamondscoutline - Twitter: @dmndscoutline

Looking to find a good designer to help with my diamondscoutline.net social media sites!
- facebook banner
- twitter banner
- instagram template (square and banner size)
- Quote or Information Template
- Committed Template (uniformed) - see the ones I made (& i am no professional) at diamondscoutline.net/committed - needs to have diamondscoutline.net logo, room for: the committed school and the team the player plays on.

Also willing to pay extra for a graphic that is the "complete package" that detail all of the steps of the recruiting process detailed in diamondscoutline.net

Font styles to use
Sans Serif

Colors
ec1f27
fbee3e

```html
<!DOCTYPE html>
<html lang="en">
<head>
<meta charset="utf-8">
<title>diamondscoutline.net – Committed Template</title>
<link rel="stylesheet" href="https://fonts.googleapis.com/css2?family=Montserrat:wght@400;900&display=swap">
<style>
  :root {
    --brand-red: #ec1f27;
    --brand-yellow: #fbee3e;
    --soft-grey: #f1f1f1;
    --paper: #ffffff;
    --ink: #0d0d0d;
  }
  html, body {
    margin: 0;
    padding: 0;
    width: 1200px;
    height: 595px;
    overflow: hidden;
    background: var(--paper);
  }
  .committed-card {
    position: relative;
    width: 1200px;
    height: 595px;
    overflow: hidden;
    background: var(--paper);
    font-family: "Montserrat", sans-serif;
  }
  .backdrop {
    position: absolute;
    inset: 0;
    width: 1200px;
    height: 595px;
  }
  .backdrop .blob-yellow { fill: var(--brand-yellow); }
  .backdrop .blob-grey { fill: var(--soft-grey); }
  .backdrop .badge-ring {
    fill: var(--paper);
    stroke: var(--brand-red);
    stroke-width: 21;
  }
  .site-name {
    position: absolute;
    left: 53px;
    top: 78px;
    margin: 0;
    font-weight: 400;
    font-size: 52px;
    line-height: 1;
    letter-spacing: 0.5px;
    color: var(--ink);
  }
  .placeholder-copy {
    position: absolute;
    left: 38px;
    top: 262px;
    width: 650px;
    margin: 0;
    text-align: center;
    font-weight: 400;
    font-size: 48px;
    line-height: 59px;
    letter-spacing: 2.4px;
    color: var(--ink);
  }
  .badge-name {
    position: absolute;
    left: 738px;
    top: 266px;
    width: 392px;
    margin: 0;
    text-align: center;
    font-weight: 400;
    font-size: 24px;
    line-height: 1.2;
    color: var(--ink);
  }
</style>
</head>
<body>
  <main class="committed-card">
    <svg class="backdrop" viewBox="0 0 1200 595" aria-hidden="true">
      <path class="blob-grey" d="M700 0 H1200 V595 H346 C300 520 300 470 340 440 C400 390 520 360 600 320 C650 290 650 240 630 200 C600 140 580 100 640 50 C670 25 690 10 700 0 Z"/>
      <path class="blob-yellow" d="M0 0 H317 C325 60 290 100 220 88 C180 82 150 60 125 100 C100 150 80 180 60 177 C40 176 28 160 22 150 C15 140 5 135 0 134 Z"/>
      <path class="blob-yellow" d="M1085 128 C1130 126 1170 128 1200 130 V595 H585 C595 545 600 520 620 505 C650 487 700 490 735 487 C760 482 752 470 748 450 C738 415 740 385 745 365 C780 290 900 250 1000 200 C1040 175 1060 150 1085 128 Z"/>
      <circle class="badge-ring" cx="934" cy="280" r="196"/>
    </svg>

    <h1 class="site-name">diamondscoutline.net</h1>

    <p class="placeholder-copy">the committed school and the team the player plays on</p>

    <p class="badge-name">diamondscoutline.net</p>
  </main>
</body>
</html>
```